Printed Circuit Board Company Web Site Design - Please see new file 82012 web design

We are a printed circuit board manufacturer. Need a company professional web site to allow our potential customers to know more about our background, capability and our products. The web site will contain three languages, which are Chinese, English and Japanese. Our audience are mainly electronic companies that procure printed circuit boards. I have a word document that have all the required text in all three languages. The final design should communicate the impression that we embrace quality, trustworthiness and long term partnership business principles.
We should have sections that allow us to post pictures of our facilities.
I have added the three files in three different languages.
Some of the information is below:
Background
RDV Harbourline Limited (RDV) was set up in Hong Kong in 2007 by two Hong Kong entrepreneurs, Mr. Tak Wong and Mr. Lok Fai. We acquired the single sided printed circuit board factory located in Dongguan City, Guangdong Province, China, from Tovand Corporation of the U.S. in 2007. In addition to RDV, Mr. Wong and Mr. Fai also own Halberd Technology Company Limited, a semiconductor company based in Hong Kong since 1997 with a total investment of over US$100 million. Halberd is engaged in the manufacturing of flexible substrates and MEMS assembly business.
RDV has been awarded TS 16949 and ISO14000 certificates since 2009 and 2004 respectively.
Business Principles
RDV Harbourline Limited strives to be a professional top notched printed circuit board supplier. We embrace four “EXCELLENCE” principles, namely, excellence in quality, excellence in prices, excellence in services and excellence in on time delivery.
We approach each customer with a long-term partnership view that delivers the lowest ownership costs and highest total values to our customers. We customize quotations and solutions in order to allow our customers to win more businesses. We believe by thinking from our customers’ points of view we will be able to create a WIN-WIN relationship.
Customers
Due to our excellent quality, services and production systems, RDV Harbourline Limited manage to service a number of large Japanese and US customers, which include:
Technical capability overview
Below is an overview of our current capability:
Target Market(s)
Electronic companies buyers
Industry/Entity Type
Business
Requirements
Must have
- Capability description
Should not have
- no cartoon

```html
<!DOCTYPE html>
<html lang="en">
<head>
<meta charset="utf-8">
<title>RDV Harbourline Limited – Printed Circuit Boards</title>
<link href="https://fonts.googleapis.com/css2?family=Arimo:wght@400;700&family=Tinos&family=Cinzel:wght@500&family=Exo+2:wght@400;500&display=swap" rel="stylesheet">
<style>
:root{
  --teal:#0b7a62;
  --teal-dark:#07604d;
  --green-tab:#0d5e3c;
  --text:#333;
  --heading:#111;
  --line:#cfcfcf;
  --login:#f8cd86;
  --white:#fff;
}
*{margin:0;padding:0;box-sizing:border-box}
html,body{width:1152px;height:1200px;overflow:hidden;background:var(--white)}
body{position:relative;font-family:"Arimo",Arial,sans-serif;color:var(--text)}
.abs{position:absolute}
.top-strip{left:0;top:0;width:1152px;height:7px;background:var(--teal)}
.brand{left:102px;top:30px;color:var(--green-tab);font-family:"Arimo",Arial,sans-serif;font-weight:700;line-height:1}
.brand-main{font-size:36px;letter-spacing:6px}
.brand-sub{font-size:14px;letter-spacing:1px;margin-top:4px}
.phone{left:896px;top:64px;display:flex;align-items:center;gap:8px;font-size:16px;color:#222}
.nav{left:96px;top:94px;width:962px;height:40px;border:1px solid var(--line);border-radius:5px;background:var(--white)}
.nav ul{list-style:none;display:flex;height:100%}
.nav li{font-family:"Cinzel",serif;font-size:14px;letter-spacing:1px;color:#222;line-height:38px}
.nav .home{position:absolute;left:29px;width:68px;height:38px;background:var(--green-tab);color:var(--white);text-align:center}
.nav .i1{position:absolute;left:153px}
.nav .i2{position:absolute;left:300px}
.nav .i3{position:absolute;left:433px}
.nav .i4{position:absolute;left:691px}
.login{position:absolute;right:0;top:0;width:85px;height:38px;background:var(--login);border-radius:0 4px 4px 0;display:flex;align-items:center;justify-content:center;gap:8px;font-weight:700;font-size:14px;color:#222}
.tagline{left:0;top:163px;width:1152px;text-align:center;font-family:"Exo 2",sans-serif;color:var(--teal);font-size:28px;letter-spacing:-.5px}
.tagline small{font-size:21px}
.principles{left:275px;top:207px;display:flex;gap:46px;font-family:"Tinos",serif;font-size:20px;color:var(--teal)}
.hero{left:100px;top:255px;width:935px;height:410px;background:radial-gradient(ellipse at center,#f4f4f4 0%,#e2e2e2 60%,#fafafa 100%);border-radius:8px}
.chev{top:428px}
.welcome-title{left:104px;top:696px;font-size:15px;font-weight:700;color:var(--heading)}
.welcome-text{left:104px;top:724px;width:512px;font-size:11.5px;line-height:14px;text-align:justify;color:#444}
.welcome-text p+p{margin-top:14px}
.photo-frame{left:656px;top:713px;width:400px;height:203px;border:1px solid var(--line)}
.photo{left:668px;top:727px;width:378px;height:175px;background:linear-gradient(135deg,#cfd6d8,#8f9da0 45%,#5c6b6a 75%,#c87a4a)}
.customers-title{left:104px;top:913px;font-size:15px;font-weight:700;color:var(--heading)}
.clients{left:112px;top:948px;width:942px;height:66px}
.client{position:absolute;font-weight:700;color:#333;font-family:"Arimo",Arial,sans-serif;line-height:1}
.footer{left:0;top:1029px;width:1152px;height:139px;background:linear-gradient(180deg,var(--teal) 0%,var(--teal-dark) 100%)}
.footer h4{position:absolute;left:104px;top:11px;color:var(--white);font-size:12px}
.links{position:absolute;top:37px;list-style:none;font-size:10.5px;color:var(--white);line-height:17.5px}
.links li::before{content:"▸ ";font-size:7px}
.address{position:absolute;right:103px;top:14px;text-align:right;color:var(--white);font-size:10.5px;line-height:17.3px}
.address strong{font-size:12px}
.copyright{left:0;top:1168px;width:1152px;height:32px;background:var(--teal-dark);color:var(--white);font-size:10.5px;font-weight:700;text-align:center;line-height:32px}
</style>
</head>
<body>
<div class="abs top-strip"></div>

<div class="abs brand">
  <div class="brand-main">RDV</div>
  <div class="brand-sub">Harbourline Limited</div>
</div>

<div class="abs phone">
  <svg width="30" height="22" viewBox="0 0 30 22"><path d="M4 14c4-8 14-9 22-4l-3 4-5-2-3 2 2 4-3 3C8 21 3 19 4 14z" fill="var(--teal)"/></svg>
  <span>(852) 3555 0142</span>
</div>

<nav class="abs nav">
  <ul>
    <li class="home">Home</li>
    <li class="i1">Products</li>
    <li class="i2">Services</li>
    <li class="i3">Technical Capabilities</li>
    <li class="i4">Contact Us</li>
  </ul>
  <div class="login">
    <svg width="18" height="22" viewBox="0 0 18 22"><path d="M4 10V6a5 5 0 0110 0v4" fill="none" stroke="#8a7a60" stroke-width="2.2"/><rect x="1" y="10" width="16" height="11" rx="2" fill="#a89478"/></svg>
    login
  </div>
</nav>

<div class="abs tagline">We embrace four "EXCELLENCE" <small>PRINCIPLES</small></div>
<div class="abs principles"><span>IN QUALITY</span><span>IN PRICES</span><span>IN SERVICES</span><span>IN ON TIME DELIVERY</span></div>

<div class="abs hero" role="img" aria-label="Banner illustration showing the customer service process: a caller, a support agent at a laptop and a satisfied customer"></div>
<svg class="abs chev" style="left:58px" width="34" height="86" viewBox="0 0 34 86"><path d="M30 2L6 43l24 41" fill="none" stroke="var(--teal)" stroke-width="6"/></svg>
<svg class="abs chev" style="left:1060px" width="34" height="86" viewBox="0 0 34 86"><path d="M4 2l24 41L4 84" fill="none" stroke="var(--teal)" stroke-width="6"/></svg>

<h2 class="abs welcome-title">WELCOME TO RDV HARBOURLINE LIMITED (RDV)</h2>
<div class="abs welcome-text">
  <p>RDV Harbourline Limited strives to be a professional top notched printed circuit board supplier. We embrace four "EXCELLENCE" principles, namely, excellence in quality, excellence in prices, excellence in services and excellence in on time delivery. printed circuit board supplier. We embrace four "EXCELLENCE" principles, namely, excellence in quality, excellence in prices.</p>
  <p>RDV Harbourline Limited strives to be a professional top notched printed circuit board supplier. We embrace four "EXCELLENCE" principles, namely, excellence in quality, excellence in prices, excellence in services and excellence in on time delivery. printed circuit board supplier. We embrace four "EXCELLENCE" principles, namely, excellence in quality, excellence in prices.</p>
</div>

<div class="abs photo-frame"></div>
<div class="abs photo" role="img" aria-label="Photo of technicians working at testing machines on the factory floor"></div>

<h2 class="abs customers-title">CUSTOMERS</h2>
<div class="abs clients">
  <svg style="position:absolute;left:0;top:22px" width="18" height="22" viewBox="0 0 18 22"><path d="M14 2L4 11l10 9" fill="none" stroke="#333" stroke-width="4"/></svg>
  <div class="client" style="left:36px;top:8px;font-size:18px">Kovashi</div>
  <div class="client" style="left:36px;top:34px;font-size:13px">Jintai Tech</div>
  <div class="client" style="left:180px;top:22px;font-size:16px">Harumoto</div>
  <div class="client" style="left:280px;top:6px;font-size:20px">Pelanova</div>
  <div class="client" style="left:300px;top:34px;font-size:18px">Shirona</div>
  <div class="client" style="left:430px;top:22px;font-size:24px">Furano</div>
  <div class="client" style="left:600px;top:18px;font-size:28px">Kendrell International</div>
  <svg style="position:absolute;left:924px;top:22px" width="18" height="22" viewBox="0 0 18 22"><path d="M4 2l10 9-10 9" fill="none" stroke="#333" stroke-width="4"/></svg>
</div>

<footer class="abs footer">
  <h4>POPULAR LINKS</h4>
  <ul class="links" style="left:104px"><li>Sitemap</li><li>Circuit Boards</li><li>Capabilities</li><li>Industries Served</li><li>About Us</li></ul>
  <ul class="links" style="left:263px"><li>Contact Us</li><li>Resources</li><li>Service Center</li><li>News &amp; Events</li><li>Privacy Policy</li></ul>
  <div class="address">
    <strong>RDV Harbourline Limited</strong><br>
    28/F Harbour Crest<br>
    12 Marlow Road<br>
    Causeway Bay, HONG KONG<br>
    Telephone: (852)35550142<br>
    Fax: (852)35550143<br>
    Email: sales@rdvharbour.com
  </div>
</footer>
<div class="abs copyright">COPYRIGHT © 2012 RDV HARBOURLINE LIMITED. ALL RIGHTS RESERVED</div>
</body>
</html>
```